Business Card Design

We need a business card designed for our new company. Prefer a black card with white logo & writing.

Contact Information for Business Card

Ted Galloway, address: 7-4812 Fernhollow Road, Abbotsford, BC, V3K 8R2, Office Phone: 604-712-3390, Cell: 604-947-2164, Email: ted@resinworkshub.ca

Colors

Designer to choose only greyscale colors for use in the design.

```html
<!DOCTYPE html>
<html lang="en">
<head>
<meta charset="utf-8">
<title>Resinworks Hub – Business Card</title>
<link rel="stylesheet" href="https://fonts.googleapis.com/css2?family=Poppins:wght@300;400;700&display=swap">
<style>
  :root {
    --stage: #1f1f20;
    --card: #1d1d20;
    --card-edge: #2c2c30;
    --ink: #ffffff;
    --ink-soft: #e2e2e2;
    --pattern-dark: #18181a;
    --pattern-light: #2e2e32;
    --corner-dark: #161618;
    --corner-light: #3a3a3e;
  }
  * { margin: 0; padding: 0; box-sizing: border-box; }
  html, body {
    width: 1200px; height: 711px; overflow: hidden;
    background: var(--stage);
    font-family: "Poppins", sans-serif;
    color: var(--ink);
  }
  .stage {
    position: relative; width: 1200px; height: 711px;
    display: flex; align-items: center; justify-content: center; gap: 40px;
  }
  .card {
    position: relative; width: 540px; height: 309px;
    background: var(--card);
    border: 1px solid var(--card-edge);
    border-radius: 4px;
    overflow: hidden;
    box-shadow: 0 14px 30px rgba(0,0,0,.55);
  }

  /* Front */
  .front__pattern {
    position: absolute; inset: 0;
    background: linear-gradient(160deg, var(--pattern-light) 0%, var(--pattern-dark) 55%, var(--pattern-light) 100%);
  }
  .front__name {
    position: absolute; inset: 0;
    display: flex; align-items: center; justify-content: center; gap: 12px;
    font-weight: 700; font-size: 38px; letter-spacing: .5px; text-transform: uppercase;
  }
  .front__mark { width: 14px; height: 14px; background: var(--ink); }

  /* Back */
  .back__brand {
    position: absolute; top: 44px; right: 34px;
    display: flex; align-items: center; gap: 8px;
    font-weight: 700; font-size: 24px; text-transform: uppercase;
  }
  .back__mark { width: 10px; height: 10px; background: var(--ink); }
  .back__contact {
    position: absolute; right: 34px; top: 112px;
    text-align: right; font-weight: 300; font-size: 12.5px; line-height: 1.5;
    color: var(--ink-soft);
  }
  .back__address { margin-bottom: 12px; }
  .contact-line { display: flex; align-items: center; justify-content: flex-end; gap: 8px; }
  .contact-line svg { width: 12px; height: 12px; fill: none; stroke: var(--ink); stroke-width: 1.6; }

  .back__corner-art {
    position: absolute; left: 0; top: 0; width: 130px; height: 309px;
    background: linear-gradient(90deg, var(--corner-dark) 0%, var(--corner-light) 100%);
  }
  .back__person {
    position: absolute; left: 30px; top: 96px;
    writing-mode: vertical-rl;
  }
  .back__person-name { font-size: 22px; font-weight: 300; line-height: 1.15; white-space: nowrap; }
  .back__person-name strong { font-weight: 700; }
  .back__person-role { font-size: 11px; font-weight: 400; padding-top: 2px; }
</style>
</head>
<body>
<main class="stage">
  <section class="card front" aria-label="Card front">
    <div class="front__pattern" role="img" aria-label="Repeating embossed chevron pattern in dark grey"></div>
    <div class="front__name"><span class="front__mark"></span>Resinworks Hub</div>
  </section>

  <section class="card back" aria-label="Card back">
    <div class="back__corner-art" role="img" aria-label="Glossy page-curl illustration along the left edge"></div>
    <div class="back__person">
      <p class="back__person-name"><strong>Ted</strong> Galloway</p>
      <p class="back__person-role">Owner</p>
    </div>

    <div class="back__brand"><span class="back__mark"></span>Resinworks Hub</div>

    <div class="back__contact">
      <p class="back__address">7-4812 Fernhollow Road,<br>Abbotsford, BC, V3K 8R2.</p>
      <p class="contact-line">604-712-3390
        <svg viewBox="0 0 12 12"><path d="M3 1.5 L4.5 4 L3.5 5 Q5 7.5 7 8.5 L8 7.5 L10.5 9 L9.5 10.5 Q4 10 1.5 3 Z"/></svg></p>
      <p class="contact-line">604-947-2164
        <svg viewBox="0 0 12 12"><rect x="3" y="1" width="6" height="10" rx="1"/><line x1="5.5" y1="9" x2="6.5" y2="9"/></svg></p>
      <p class="contact-line">www.resinworkshub.ca
        <svg viewBox="0 0 12 12"><circle cx="6" cy="6" r="4.8"/><ellipse cx="6" cy="6" rx="2" ry="4.8"/><line x1="1.2" y1="6" x2="10.8" y2="6"/></svg></p>
      <p class="contact-line">ted@resinworkshub.ca
        <svg viewBox="0 0 12 12"><rect x="1" y="2.5" width="10" height="7"/><path d="M1 2.5 L6 6.5 L11 2.5"/></svg></p>
    </div>
  </section>
</main>
</body>
</html>
```